Healthy lifestyle Influencer business card

I need your creativity to have a business card that I can leave in all the restaurants, hotels and spas I visit to inform them that I am an influencer specializing in the wellness sector and that I will write a review about them. You can use my instagram photos Lunavita27 or on my website www.piattileggeriorto.it. I would like my business card to impress with its creativity! thank you very much!

Contact Information for Business Card

siteweb, instagram, phone number

Font styles to use
Decorative
Script

Colors
0094D4
00A9DD
6FCCEA
C7EBF8
E9F6FB
59FF00
82FF00
B8FF75
E3FFCB
F4FFEA
FFC000
F8CF3A
FAE287
FDF2CF
FEFAEE
F0912C
F2A743
F7CA91
FBE8D2
FDF5EE
EE7325
F08F49
F5BC92
FAE3D3
FDF4ED
EB3D1F
EC4F4E
F09395
F8D3D4
FCEDEE
E54698
E96AAD
F1A4CE
F9D9EA
FCEFF6

Requirements
Nice to have
• creativity

```html
<!DOCTYPE html>
<html lang="it">
<head>
<meta charset="utf-8">
<title>Luna Vita Chef – biglietto da visita</title>
<link rel="stylesheet" href="https://fonts.googleapis.com/css2?family=Great+Vibes&family=Roboto:wght@300;400&family=Quicksand:wght@500&display=swap">
<style>
  :root{
    --backdrop:#2d2d2d;
    --sage:#8fb5ab;
    --sage-deep:#7fa89d;
    --sage-icon:#86aea4;
    --paper:#efefee;
    --paper-shade:#e2e2e1;
    --ink:#3f4442;
    --ink-soft:#4e5553;
    --edge:#4a4a4a;
    --photo-cream:#e7e1dc;
    --photo-cake:#d9b7a4;
    --photo-berry:#6b5a48;
    --photo-tart:#b8a9b4;
    --photo-mousse:#b7825c;
    --photo-cookie:#e6d7c2;
  }
  *{margin:0;padding:0;box-sizing:border-box}
  html,body{width:1200px;height:1138px;overflow:hidden;background:var(--backdrop)}
  .canvas{position:relative;width:1200px;height:1138px}

  .card{position:absolute;border-radius:16px;overflow:hidden}

  /* Front */
  .card-front{left:272px;top:184px;width:622px;height:376px;background:var(--sage)}
  .photo{position:absolute;width:185px;height:104px;border-radius:3px}
  .photo-mousse-bowl{left:24px;top:22px;background:linear-gradient(135deg,var(--photo-cream),#cdb6ad)}
  .photo-red-velvet{left:219px;top:22px;background:linear-gradient(135deg,#e8dcd2,var(--photo-cake))}
  .photo-berry-cup{left:415px;top:22px;background:linear-gradient(135deg,var(--photo-berry),#4a4e6a)}
  .photo-blueberry-tart{left:24px;top:135px;background:linear-gradient(180deg,#5d6175,var(--photo-tart) 55%,#e4e2e3)}
  .photo-cake-tin{left:219px;top:135px;background:radial-gradient(ellipse at center,#c99470,var(--photo-mousse) 60%,#6a4a2e)}
  .photo-coconut-cookies{left:415px;top:135px;background:linear-gradient(135deg,#f2ede6,var(--photo-cookie))}

  .brand{position:absolute;left:0;right:0;text-align:center;color:var(--ink)}
  .brand-name{top:282px;font:300 34px/1 "Roboto",sans-serif;letter-spacing:1px}
  .brand-tagline{top:323px;font:500 13px/1 "Quicksand",sans-serif}

  /* Back */
  .card-back{left:274px;top:606px;width:620px;height:375px;background:linear-gradient(180deg,var(--paper),var(--paper-shade))}
  .back-curve{position:absolute;inset:0}
  .person-name{position:absolute;left:35px;top:46px;font:400 44px/1 "Great Vibes",cursive;color:var(--ink)}
  .contact-list{position:absolute;left:35px;top:218px;list-style:none;font:300 14px/21px "Roboto",sans-serif;color:var(--ink-soft)}
  .contact-list li{display:flex;align-items:center;gap:10px}
  .contact-list svg{width:12px;height:12px;flex:none}
  .vat{position:absolute;left:35px;top:288px;font:300 14px/1 "Roboto",sans-serif;color:var(--ink-soft)}
  .social{position:absolute;left:35px;top:322px;display:flex;align-items:center;gap:10px;font:300 16px/1 "Roboto",sans-serif;color:var(--ink-soft)}
  .social-dot{width:14px;height:14px;border-radius:50%;background:var(--sage-deep)}

  .vertical-brand{position:absolute;left:494px;top:188px;width:320px;transform:translate(-50%,-50%) rotate(90deg);text-align:center;color:var(--ink)}
  .vertical-brand .brand-name-v{font:300 35px/1 "Roboto",sans-serif;letter-spacing:1px;display:block}
  .vertical-brand .brand-tagline-v{font:500 13px/1 "Quicksand",sans-serif;display:block;margin-top:14px}
</style>
</head>
<body>
<div class="canvas">

  <section class="card card-front">
    <div class="photo photo-mousse-bowl" role="img" aria-label="Foto: coppette di mousse al cioccolato con cucchiaino"></div>
    <div class="photo photo-red-velvet" role="img" aria-label="Foto: torta red velvet tagliata a fetta"></div>
    <div class="photo photo-berry-cup" role="img" aria-label="Foto: bicchierino di dessert con mirtilli e lamponi"></div>
    <div class="photo photo-blueberry-tart" role="img" aria-label="Foto: cheesecake ricoperta di mirtilli"></div>
    <div class="photo photo-cake-tin" role="img" aria-label="Foto: impasto di torta in uno stampo a cerniera"></div>
    <div class="photo photo-coconut-cookies" role="img" aria-label="Foto: biscotti al cocco"></div>
    <p class="brand brand-name">Luna Vita Chef</p>
    <p class="brand brand-tagline">Leggera con i piatti che ami</p>
  </section>

  <section class="card card-back">
    <svg class="back-curve" viewBox="0 0 620 375" preserveAspectRatio="none" aria-hidden="true">
      <path d="M442 0 Q300 190 452 375 L620 375 L620 0 Z" fill="var(--edge)"/>
      <path d="M462 0 Q322 190 456 375 L620 375 L620 0 Z" fill="var(--sage)"/>
    </svg>

    <h1 class="person-name">Luna Ferraro</h1>

    <ul class="contact-list">
      <li>
        <svg viewBox="0 0 12 12" aria-hidden="true"><path d="M1 4 Q6 0 11 4 L9 5.5 L8 4.5 H4 L3 5.5 Z M2.5 6.5 H9.5 L10.5 11 H1.5 Z" fill="var(--sage-icon)"/></svg>
        000-0000-0000
      </li>
      <li>
        <svg viewBox="0 0 12 12" aria-hidden="true"><rect x="0.5" y="2.5" width="11" height="7.5" fill="var(--sage-icon)"/><path d="M0.5 2.5 L6 7 L11.5 2.5" fill="none" stroke="#fff" stroke-width="1"/></svg>
        ciao@piattileggeriorto.it
      </li>
      <li>
        <svg viewBox="0 0 12 12" aria-hidden="true"><circle cx="6" cy="6" r="5" fill="none" stroke="var(--sage-icon)" stroke-width="1.2"/><ellipse cx="6" cy="6" rx="2" ry="5" fill="none" stroke="var(--sage-icon)" stroke-width="1"/><path d="M1 6 H11" stroke="var(--sage-icon)" stroke-width="1"/></svg>
        www.piattileggeriorto.it
      </li>
    </ul>

    <p class="vat">Partita IVA 01234560789</p>

    <p class="social"><span class="social-dot" aria-hidden="true"></span>@Lunavita27</p>

    <div class="vertical-brand">
      <span class="brand-name-v">Luna Vita Chef</span>
      <span class="brand-tagline-v">Leggera con i piatti che ami</span>
    </div>
  </section>

</div>
</body>
</html>
```